Business Card Re-Design/Update

We'd like to update out business cards. I've included our current "Style guide" which has the colour scheme of the organisation in it. I've also included the branding files with logos etc in them.

I've also included a copy of one of our existing cards so that you can see how ugly/dated they look. I'd like a fresh modern corporate look.

Target Market(s)

These are for our clients, potential clients, industry contacts - like all business cards

Contact Information for Business Card

Name
Position
Company Address - Level 1, 47 Fernby Street, Carlow Qld 4072
Direct Phone
mobile
Email
Website -www.korvalit.com.au
Logo

Colors

Designer to choose colors to be used in the design.

Requirements
Must have
• Main Logo
• Cards will need to be editable to be able to personalize them for each new employee.
Nice to have
• The MapOut, ShipWell, KeepSteady would be okay to have if they can be sensibly and professionally added to the look without detracting from the main imagery.
• Maybe they could go on the back of the card? will leave this to your creative discretion as to whether/where they fit.
Should not have
• Should not have decorative or script fonts

```html
<!DOCTYPE html>
<html lang="en">
<head>
<meta charset="utf-8">
<title>KorvalIT Business Card</title>
<link href="https://fonts.googleapis.com/css2?family=Arimo:ital,wght@0,400;0,700;1,400&display=swap" rel="stylesheet">
<style>
  :root {
    --brand-red: #d9262e;
    --charcoal: #4a4a4c;
    --charcoal-dark: #2b2b2d;
    --card-white: #f4f4f4;
    --text-grey: #555557;
    --stage: #1c1c1d;
  }
  * { margin: 0; padding: 0; box-sizing: border-box; }
  html, body {
    width: 1200px; height: 900px; overflow: hidden;
    background: var(--stage);
    font-family: "Arimo", Arial, sans-serif;
  }
  .card {
    position: absolute; left: 250px; width: 700px; height: 400px;
    border-radius: 4px; overflow: hidden;
    box-shadow: 0 12px 30px rgba(0,0,0,.5);
  }
  .card--front { top: 40px; background: var(--card-white); }
  .card--back {
    top: 470px;
    background: radial-gradient(ellipse at 40% 30%, #3a3a3c 0%, var(--charcoal-dark) 70%, #222224 100%);
  }
  .card__shapes { position: absolute; inset: 0; width: 100%; height: 100%; }

  .brand { position: absolute; display: flex; align-items: center; gap: 16px; }
  .brand__mark { width: 44px; height: 44px; background: var(--brand-red); }
  .brand__name { font-weight: 700; letter-spacing: -1px; }
  .card--front .brand { left: 48px; top: 44px; }
  .card--front .brand__name { font-size: 62px; color: var(--text-grey); }

  .person { position: absolute; left: 48px; top: 150px; }
  .person__name { color: var(--brand-red); font-weight: 700; font-size: 22px; }
  .person__role { color: var(--text-grey); font-style: italic; font-size: 15px; margin-top: 4px; }

  .contact { position: absolute; left: 48px; top: 238px; list-style: none; color: #fff; font-size: 15px; line-height: 23px; }
  .contact li { display: flex; align-items: center; gap: 10px; }
  .contact svg { width: 14px; height: 14px; fill: var(--brand-red); flex: none; }
  .address { position: absolute; left: 330px; top: 262px; color: #fff; font-size: 15px; line-height: 21px; font-style: normal; }

  .card--back .brand { left: 50%; top: 140px; transform: translateX(-50%); }
  .card--back .brand__name { font-size: 72px; color: #e6e6e6; }
  .tagline { position: absolute; left: 0; right: 0; top: 250px; text-align: center; color: #e6e6e6; font-size: 18px; font-style: italic; }
  .tagline span { color: var(--brand-red); font-style: normal; }
</style>
</head>
<body>

<section class="card card--front" aria-label="Card front">
  <svg class="card__shapes" viewBox="0 0 700 400" aria-hidden="true">
    <defs>
      <linearGradient id="bandFill" x1="0" x2="1" y1="0" y2="0">
        <stop offset="0" stop-color="#3a3a3c"/>
        <stop offset="1" stop-color="#5c5c5e"/>
      </linearGradient>
    </defs>
    <polygon points="0,220 560,220 510,355 0,355" fill="url(#bandFill)"/>
    <polygon points="700,250 700,400 560,400" fill="var(--brand-red)"/>
  </svg>

  <div class="brand">
    <span class="brand__mark"></span>
    <span class="brand__name">KorvalIT</span>
  </div>

  <div class="person">
    <p class="person__name">Marla Quinton</p>
    <p class="person__role">Business Development Manager</p>
  </div>

  <ul class="contact">
    <li><svg viewBox="0 0 16 16"><rect x="1" y="3" width="14" height="10" rx="1"/></svg>+61 (0) 7 3390 4728</li>
    <li><svg viewBox="0 0 16 16"><path d="M3 1l3 3-2 2c1 2 3 4 5 5l2-2 3 3-2 3C6 15 1 10 1 3z"/></svg>+61 (0) 412 557 903</li>
    <li><svg viewBox="0 0 16 16"><path d="M1 3h14v10H1zM1 3l7 6 7-6" /></svg>mquinton@korvalit.com.au</li>
    <li><svg viewBox="0 0 16 16"><circle cx="8" cy="8" r="7"/></svg>www.korvalit.com.au</li>
  </ul>

  <address class="address">Level 1, 47 Fernby Street,<br>Carlow Qld 4072</address>
</section>

<section class="card card--back" aria-label="Card back">
  <div class="brand">
    <span class="brand__mark"></span>
    <span class="brand__name">KorvalIT</span>
  </div>
  <p class="tagline">The MapOut<span>,</span> ShipWell<span>,</span> KeepSteady</p>
</section>

</body>
</html>
```